Creative, fresh business card design for Ripplecraft Facades

We need a fresh, creative business card design for Ripplecraft Facades. We are the manufacturer of Ripplecraft Facades in Australia. Wall panels are 2400 x 1200mm panels made from MDF and feature 3D patterns on the face of the panel. The colours to be used are green, silver/grey and white RGB
Red 187
Green 207
Blue 65.

An idea is to possibly use a watermark of one of our designs as a background (like on the "Grids" design on the left hand side of page 2 of our brochure).

Target Market(s)

Interior designers, architects, builders and home renovators

Industry/Entity Type

Business

Contact Information for Business Card

Details to go on the card are:
Our logo (attached),
Slogan: "Decorative panels for interiors and exteriors",
Contact name,
Position,
Mobile phone number,
Business address,
Business phone,
Business fax,
Website and
Email address.

I have attached a few images of our panels and our brochure for reference.

The colours of the business card should feature our logo colours which are: RGB
Red 187
Green 207
Blue 65

Requirements
Must have
• Very modern fonts and design. Some of the designs shown especially the "Prisms" design which is a popular design.
Nice to have
• Creative but simple design. Very contemporary.
Should not have
• Anything ornate or old fashioned.

```html
<!DOCTYPE html>
<html lang="en">
<head>
<meta charset="UTF-8">
<title>Ripplecraft Facades – Business Card</title>
<link rel="stylesheet" href="https://fonts.googleapis.com/css2?family=Open+Sans:wght@400;600;700&display=swap">
<style>
  :root {
    --backdrop: #2b2b2d;
    --card: #ffffff;
    --lime: #bbcf41;
    --lime-soft: #cddd6a;
    --silver: #9c9ea2;
    --silver-light: #b9bbbe;
    --ink: #4a4b4e;
    --ink-soft: #6f7074;
  }
  * { box-sizing: border-box; margin: 0; padding: 0; }
  html, body {
    width: 1200px; height: 1000px; overflow: hidden;
    background: var(--backdrop);
    font-family: "Open Sans", Arial, sans-serif;
  }
  .business-card {
    position: absolute; left: 150px; top: 242px;
    width: 900px; height: 515px;
    background: var(--card);
    border-radius: 34px;
    overflow: hidden;
  }
  .side-swoosh { position: absolute; inset: 0; }
  .brand {
    position: absolute; left: 215px; top: 88px;
  }
  .brand-row { display: flex; align-items: center; gap: 14px; }
  .brand-mark { width: 34px; height: 34px; background: var(--lime); }
  .brand-name { font-size: 30px; font-weight: 600; color: var(--ink); letter-spacing: 0.2px; }
  .brand-tagline {
    margin-top: 8px; margin-left: 48px;
    font-size: 14px; letter-spacing: 2px; color: var(--silver); line-height: 1.35;
  }
  .person {
    position: absolute; right: 360px; top: 262px; text-align: right;
  }
  .person-name { font-size: 34px; font-weight: 700; color: var(--ink); line-height: 1.1; }
  .person-name .surname { color: var(--lime); }
  .person-role { font-size: 19px; color: var(--ink-soft); margin-top: 2px; }
  .address {
    position: absolute; right: 360px; top: 370px;
    display: flex; align-items: flex-end; gap: 14px;
  }
  .address-text { text-align: right; font-size: 18px; line-height: 1.35; color: var(--ink-soft); }
  .address-icon { width: 30px; height: 30px; margin-bottom: 2px; }
  .divider {
    position: absolute; left: 568px; top: 258px;
    width: 2px; height: 160px; background: var(--ink-soft);
  }
  .contacts {
    position: absolute; left: 600px; top: 250px;
    list-style: none;
  }
  .contacts li {
    display: flex; align-items: center; gap: 16px;
    font-size: 18px; color: var(--ink-soft); height: 33px;
  }
  .contacts svg { width: 18px; height: 18px; flex: none; }
</style>
</head>
<body>
  <div class="business-card">
    <svg class="side-swoosh" viewBox="0 0 900 515" aria-hidden="true">
      <path d="M0,0 L250,0 C120,120 110,370 350,515 L0,515 Z" fill="var(--silver)"/>
      <path d="M0,0 L250,0 C125,110 85,330 245,515 L0,515 Z" fill="var(--lime-soft)"/>
      <path d="M0,0 L250,0 C150,90 60,300 205,515 L0,515 Z" fill="var(--lime)"/>
    </svg>

    <div class="brand">
      <div class="brand-row">
        <div class="brand-mark"></div>
        <div class="brand-name">Ripplecraft Facades</div>
      </div>
      <div class="brand-tagline">decorative panels for<br>interiors &amp; landscapes</div>
    </div>

    <div class="person">
      <div class="person-name">Daniel <span class="surname">Ward</span></div>
      <div class="person-role">Director</div>
    </div>

    <div class="address">
      <svg class="address-icon" viewBox="0 0 30 30" aria-hidden="true">
        <path d="M27 3 L3 13 L13 16 L16 27 Z" fill="none" stroke="var(--lime)" stroke-width="1.8" stroke-linejoin="round"/>
        <path d="M13 16 L27 3" stroke="var(--lime)" stroke-width="1.8"/>
      </svg>
      <div class="address-text">Your Street Address<br>New York, 1234</div>
    </div>

    <div class="divider"></div>

    <ul class="contacts">
      <li>
        <svg viewBox="0 0 18 18" aria-hidden="true"><rect x="5" y="1" width="8" height="16" rx="1.5" fill="none" stroke="var(--lime)" stroke-width="1.6"/><circle cx="9" cy="14" r="1" fill="var(--lime)"/></svg>
        +000 123 456 789
      </li>
      <li>
        <svg viewBox="0 0 18 18" aria-hidden="true"><path d="M4 2 L7 2 L8 6 L6 7.5 C7 10 8 11 10.5 12 L12 10 L16 11 L16 14 C16 15 15 16 14 16 C8 16 2 10 2 4 C2 3 3 2 4 2 Z" fill="var(--lime)"/></svg>
        +000 123 456 789
      </li>
      <li>
        <svg viewBox="0 0 18 18" aria-hidden="true"><rect x="5" y="2" width="8" height="5" fill="none" stroke="var(--lime)" stroke-width="1.5"/><rect x="2" y="7" width="14" height="9" rx="1.5" fill="var(--lime)"/></svg>
        +000 123 456 789
      </li>
      <li>
        <svg viewBox="0 0 18 18" aria-hidden="true"><rect x="1.5" y="4" width="15" height="11" rx="1" fill="var(--lime)"/><path d="M2 5 L9 10.5 L16 5" fill="none" stroke="#fff" stroke-width="1.4"/></svg>
        yourname@email.com
      </li>
      <li>
        <svg viewBox="0 0 18 18" aria-hidden="true"><circle cx="10.5" cy="7.5" r="5" fill="none" stroke="var(--lime)" stroke-width="2"/><path d="M7 11 L2 16" stroke="var(--lime)" stroke-width="2.4" stroke-linecap="round"/></svg>
        www.websitename.com
      </li>
    </ul>
  </div>
</body>
</html>
```